SaaS Early tech startup business card design

Unique design for experience ecommerce platform company. the business cards will be used by executive members. conformance with color code is required.

```html
<!DOCTYPE html>
<html lang="en">
<head>
<meta charset="utf-8">
<title>kivo business card</title>
<link href="https://fonts.googleapis.com/css2?family=Roboto:wght@400;700&display=swap" rel="stylesheet">
<style>
  :root {
    --backdrop: #1c1c1c;
    --card: #2c2a2a;
    --card-tint: #363434;
    --brand-teal: #1fb3a3;
    --brand-blue: #1477a8;
    --text-light: #e6e6e6;
    --rule: #1a6f9c;
  }
  html, body {
    margin: 0;
    width: 1200px;
    height: 874px;
    overflow: hidden;
    background: var(--backdrop);
    font-family: "Roboto", Arial, sans-serif;
  }
  .canvas {
    position: relative;
    width: 1200px;
    height: 874px;
  }
  .card {
    position: absolute;
    left: 280px;
    width: 640px;
    height: 366px;
    background: var(--card);
    overflow: hidden;
  }
  .card--front { top: 51px; }
  .card--back { top: 457px; }

  .front-pattern {
    position: absolute;
    inset: 0;
    background: radial-gradient(ellipse at 40% 45%, var(--card-tint) 0%, var(--card) 75%);
  }
  .wordmark {
    position: absolute;
    left: 0;
    right: 0;
    text-align: center;
    font-weight: 700;
    color: var(--brand-teal);
    letter-spacing: -2px;
    line-height: 1;
    margin: 0;
  }
  .card--front .wordmark {
    top: 108px;
    font-size: 150px;
  }
  .card--back .wordmark {
    top: 40px;
    font-size: 130px;
  }

  .identity {
    position: absolute;
    right: 340px;
    top: 205px;
    text-align: right;
  }
  .identity__name {
    margin: 0;
    font-size: 24px;
    font-weight: 700;
    color: var(--brand-blue);
  }
  .identity__role {
    margin: 2px 0 8px;
    font-size: 16px;
    color: var(--brand-teal);
  }
  .identity__address {
    font-style: normal;
    font-size: 15px;
    line-height: 1.35;
    color: var(--text-light);
  }
  .divider {
    position: absolute;
    left: 320px;
    top: 205px;
    width: 1px;
    height: 110px;
    background: var(--rule);
  }
  .contacts {
    position: absolute;
    left: 340px;
    top: 214px;
    margin: 0;
    padding: 0;
    list-style: none;
    font-size: 15px;
    line-height: 24px;
    color: var(--text-light);
  }
  .contacts li {
    display: flex;
    align-items: center;
    gap: 9px;
  }
  .contacts svg {
    width: 13px;
    height: 13px;
    fill: var(--brand-teal);
    flex: none;
  }
</style>
</head>
<body>
<main class="canvas">
  <section class="card card--front">
    <div class="front-pattern" role="img" aria-label="Subtle dark checkered background pattern"></div>
    <p class="wordmark">kivo</p>
  </section>

  <section class="card card--back">
    <p class="wordmark">kivo</p>

    <div class="identity">
      <h1 class="identity__name">Daniel Reyes</h1>
      <p class="identity__role">President</p>
      <address class="identity__address">412 Birchwood Road<br>Juneau, Alaska 56120</address>
    </div>

    <div class="divider"></div>

    <ul class="contacts">
      <li>
        <svg viewBox="0 0 16 16" aria-hidden="true"><path d="M3.6 1l2.6 3-1.4 2.1c.9 1.9 2.2 3.2 4.1 4.1L11 8.8l3 2.6-1.2 2.9C7 14.6 1.4 9 1.7 2.2z"/></svg>
        555-204-7731
      </li>
      <li>
        <svg viewBox="0 0 16 16" aria-hidden="true"><path d="M4 1h8v14H4zM5.5 2.5v9h5v-9zM7.2 12.6h1.6v1.2H7.2z" fill-rule="evenodd"/></svg>
        555-318-6642
      </li>
      <li>
        <svg viewBox="0 0 16 16" aria-hidden="true"><path d="M1 3h14v10H1zM2.5 4.5L8 8.7l5.5-4.2v-.1h-11zM2.5 6.3v5.2h11V6.3L8 10.5z" fill-rule="evenodd"/></svg>
        name@kivo.com
      </li>
      <li>
        <svg viewBox="0 0 16 16" aria-hidden="true"><path d="M8 1a7 7 0 110 14A7 7 0 018 1zm0 1.5a5.5 5.5 0 100 11 5.5 5.5 0 000-11zM2.6 7h10.8v2H2.6zM7 2.6h2v10.8H7z" fill-rule="evenodd"/></svg>
        www.kivo.com
      </li>
    </ul>
  </section>
</main>
</body>
</html>
```